Dental Implant Logo and Business Card for Local Dentist

Design a unique business card and a logo that incorporates a dental implant as a primary focal point or a part of the text. New logo design & business card needs to incorporate our businesses old star shaped logo (attached) and a dental implant, along with our business name. Star logo does not have to remain the exact same colors and can be any size. Looking for a warm, friendly (non-aggressive) design that uses colors in the blue-green palate, partial to mint-turquoise color similar to the images attached . SIMPLE IS GOOD, but looking for creativity to bring all the elements together. OK to incorporate a splash of color. I have attached a few images of implant logos I like along with our existing star shaped logo. *I have also uploaded some images that represent local landscapes & images for the back of the business card. I would like to include a silhouette or sketch that represents one one of these areas on the back of the business card to convey the connection to our community and local roots of our business since we are 4th generation members of this community . Can visit our dental practice website for more info. www.hartwellandodegarddentalcare.example Card Must Haves on Front of Card:1. business name "Hartwell & Odegard Dental Care" 2. My Name: "Colin Odegard D.D.S."3. Phone # (925) 754-6020Other info for card (can be front or back)Address: 7840 Quarry Ridge Rd. #2C Brookdale, Ca 94531e-mail: millerandsimarrodentalcare@gmail.comcosmetic, family, & impDesign a unique business card and a logo that incorporates a dental implant as a primary focal point or a part of the text. New logo design & business card needs to incorporate our businesses old star shaped logo (attached) and a dental implant, along with our business name. Star logo does not have to remain the exact same colors and can be any size. Looking for a warm, friendly (non-aggressive) design that uses colors in the blue-green palate, partial to mint-turquoise color similar to the images attached . SIMPLE IS GOOD, but looking for creativity to bring all the elements together. OK to incorporate a splash of color. I have attached a few images of implant logos I like along with our existing star shaped logo. *I have also uploaded some images that represent local landscapes & images for the back of the business card. I would like to include a silhouette or sketch that represents one one of these areas on the back of the business card to convey the connection to our community and local roots of our business since we are 4th generation members of this community . Can visit our dental practice website for more info. www.hartwellandodegarddentalcare.example Card Must Haves on Front of Card:1. business name "Hartwell & Odegard Dental Care" 2. My Name: "Colin Odegard D.D.S."3. Phone # (925) 754-6020Other info for card (can be front or back)Address: 7840 Quarry Ridge Rd. #2C Brookdale, Ca 94531e-mail: millerandsimarrodentalcare@gmail.comcosmetic, family, & implant dentistry

Target Market(s)

Families

Industry/Entity Type

Dental

Contact Information for Business Card

See Project description above

Logo Text

Hartwell & Odegard Dental Care

Font styles to use
Serif

Colors
ffffff
33b8a4
87cfc6
0492cd
33a6d7
0255a3

Requirements
Must have
• *See Description...
• Card Must Haves on Front of Card:
• 1. business name "Hartwell & Odegard Dental Care"
• 2. My Name: "Colin Odegard D.D.S."
• 3. Phone # (555) 318-4297
• Other info for card (can be front or back)
• Address: 7840 Quarry Ridge Rd. #2C Brookdale, Ca 90217
• e-mail: hartwellandodegarddentalcare@example-mail.com
Nice to have
• Local image sketch or silhouette on back side of business card with remaining information on back: address, website, e-mail etc.

```html
<!DOCTYPE html>
<html lang="en">
<head>
<meta charset="utf-8">
<title>Hartwell &amp; Odegard Dental Care — Business Card</title>
<link href="https://fonts.googleapis.com/css2?family=Tinos:wght@700&family=Roboto:wght@400;500&display=swap" rel="stylesheet">
<style>
  :root{
    --white:#ffffff;
    --mint:#33b8a4;
    --mint-light:#87cfc6;
    --blue:#0492cd;
    --sky:#33a6d7;
    --navy:#0255a3;
    --ink:#1a1a1a;
  }
  html,body{margin:0;padding:0;overflow:hidden;background:var(--white);}
  .canvas{position:relative;width:1200px;height:399px;overflow:hidden;background:var(--white);}
  .shapes{position:absolute;inset:0;}
  .brand-mark{position:absolute;left:256px;top:60px;width:48px;height:48px;border-radius:50%;background:var(--sky);}
  .brand-name{position:absolute;left:110px;top:212px;width:344px;text-align:center;
    font-family:"Tinos","Times New Roman",serif;font-weight:700;color:var(--navy);
    font-size:31px;line-height:34px;margin:0;}
  .brand-name .line{display:block;}
  .brand-name .rule{display:block;width:320px;height:3px;background:var(--navy);margin:4px auto 4px;}
  .doctor{position:absolute;left:668px;top:76px;font-family:"Roboto",Arial,sans-serif;color:var(--ink);}
  .doctor-name{font-size:21px;font-weight:400;margin:0;padding:0 0 4px 0;width:196px;border-bottom:1.5px solid var(--ink);}
  .doctor-title{font-size:21px;margin:6px 0 0 0;}
  .contact{position:absolute;right:24px;top:290px;margin:0;padding:0;list-style:none;
    font-family:"Roboto",Arial,sans-serif;font-size:9.5px;font-weight:500;color:var(--ink);}
  .contact li{display:flex;align-items:center;justify-content:flex-end;gap:8px;margin-bottom:12px;text-align:right;line-height:12px;}
  .contact svg{width:12px;height:12px;flex:none;}
</style>
</head>
<body>
<div class="canvas">
  <svg class="shapes" viewBox="0 0 1200 399" width="1200" height="399" aria-hidden="true">
    <polygon points="0,43 209,37 97,227 0,183" fill="var(--blue)"/>
    <polygon points="0,43 110,40 40,150 0,183" fill="var(--sky)"/>
    <polygon points="32,399 129,302 194,399" fill="var(--mint)"/>
    <polygon points="442,162 583,39 583,302" fill="var(--mint-light)"/>
    <polygon points="626,0 1000,0 626,236" fill="var(--mint-light)"/>
    <polygon points="872,222 1200,183 1200,399 928,399" fill="var(--mint)"/>
    <polygon points="912,286 1200,252 1200,399 936,399" fill="var(--white)"/>
  </svg>

  <div class="brand-mark"></div>
  <p class="brand-name"><span class="line">Hartwell &amp; Odegard</span><span class="rule"></span><span class="line">Dental Care</span></p>

  <div class="doctor">
    <p class="doctor-name">Colin Odegard</p>
    <p class="doctor-title">D.D.S</p>
  </div>

  <ul class="contact">
    <li><span>Address: 7840 Quarry Ridge Rd.<br>#2C Brookdale, Ca 90217</span>
      <svg viewBox="0 0 12 12"><path d="M6 0.5a4 4 0 0 1 4 4c0 3-4 7-4 7s-4-4-4-7a4 4 0 0 1 4-4z" fill="var(--ink)"/><circle cx="6" cy="4.5" r="1.5" fill="var(--white)"/></svg></li>
    <li><span>www.hartwellandodegarddentalcare.example</span>
      <svg viewBox="0 0 12 12"><circle cx="6" cy="6" r="5" fill="none" stroke="var(--ink)" stroke-width="1"/><ellipse cx="6" cy="6" rx="2.2" ry="5" fill="none" stroke="var(--ink)" stroke-width="1"/><line x1="1" y1="6" x2="11" y2="6" stroke="var(--ink)" stroke-width="1"/></svg></li>
    <li><span>hartwellandodegarddentalcare@example-mail.com</span>
      <svg viewBox="0 0 12 12"><rect x="0.5" y="2.5" width="11" height="7.5" fill="var(--ink)"/><polyline points="0.5,2.5 6,7 11.5,2.5" fill="none" stroke="var(--white)" stroke-width="1"/></svg></li>
    <li><span>(555) 318-4297</span>
      <svg viewBox="0 0 12 12"><rect x="3" y="0.5" width="6" height="11" rx="1" fill="var(--ink)"/><rect x="4" y="2" width="4" height="7" fill="var(--white)"/></svg></li>
  </ul>
</div>
</body>
</html>
```